Local Roofing/Construction company business needs new biz card design

We need a new business card design, current cards are from the start of this operation and generic at best. We are a local Construction Company (General Contractor) with a majority of our work originating from insurance claims-exterior finish work is the main focus (Roofs-Siding-Gutters etc). Heavily involved with homeowners and the low ball offers they receive from insurance company's after a insurable event takes place. I have attached some of our original logo file(s) below.

```html
<!DOCTYPE html>
<html lang="en">
<head>
<meta charset="utf-8">
<title>Tallow Ridge Builders – Business Card</title>
<link rel="stylesheet" href="https://fonts.googleapis.com/css2?family=Montserrat:wght@400;500;700;800&display=swap">
<style>
  :root {
    --green: #22d672;
    --ink: #1f1f1f;
    --card-dark: #262626;
    --paper: #ffffff;
    --muted: #555555;
    --backdrop: #e6e4e1;
  }
  * { box-sizing: border-box; margin: 0; padding: 0; }
  html, body { width: 1200px; height: 786px; overflow: hidden; }
  body {
    background: var(--backdrop);
    font-family: "Montserrat", Arial, sans-serif;
    position: relative;
  }
  .card {
    position: absolute;
    top: 243px;
    width: 520px;
    height: 300px;
    overflow: hidden;
    box-shadow: 0 6px 18px rgba(0,0,0,0.18);
  }
  .card--front { left: 60px; background: var(--paper); }
  .card--back { left: 620px; background: var(--card-dark); }
  .card__edge {
    position: absolute; left: 0; right: 0; bottom: 0;
    height: 7px; background: var(--green);
  }
  .brand {
    display: flex; align-items: center; gap: 12px;
    font-weight: 800; text-transform: uppercase; line-height: 1.05;
  }
  .brand__mark { background: var(--green); flex: none; }
  .card--front .brand {
    position: absolute; left: 34px; top: 34px;
    color: var(--ink); font-size: 28px; letter-spacing: 0.5px;
  }
  .card--front .brand__mark {
    position: absolute; left: 358px; top: 6px;
    width: 116px; height: 116px;
  }
  .card--back .brand {
    position: absolute; left: 60px; top: 112px;
    color: var(--paper); font-size: 32px; letter-spacing: 0.5px;
  }
  .card--back .brand__mark { width: 46px; height: 46px; }
  .contact {
    position: absolute; left: 34px; top: 130px;
    font-size: 11.5px; color: var(--muted); line-height: 1.35;
  }
  .contact__tab {
    position: absolute; left: 0; top: 134px;
    width: 8px; height: 26px; background: var(--green);
  }
  .contact__name { color: var(--green); font-weight: 700; font-size: 19px; line-height: 1.1; }
  .contact__role { font-size: 11.5px; margin-bottom: 10px; }
  .contact__address { margin-bottom: 10px; }
  .contact__list { list-style: none; }
  .contact__list li { display: flex; align-items: center; gap: 8px; }
  .contact__list svg { width: 10px; height: 10px; fill: var(--green); flex: none; }
</style>
</head>
<body>
  <section class="card card--front" aria-label="Card front">
    <div class="brand">
      <span>Tallow Ridge<br>Builders</span>
      <span class="brand__mark"></span>
    </div>
    <span class="contact__tab"></span>
    <div class="contact">
      <p class="contact__name">Dana Whitford</p>
      <p class="contact__role">Owner</p>
      <p class="contact__address">48 Orchard Bend Ln<br>Lakemont, MO 63301</p>
      <ul class="contact__list">
        <li><svg viewBox="0 0 10 10"><path d="M2 0.5 L3.8 2.6 L2.9 3.8 Q4 6 6.2 7.1 L7.4 6.2 L9.5 8 L8.3 9.5 Q1.5 8.5 0.5 1.7 Z"/></svg>555-210-4478</li>
        <li><svg viewBox="0 0 10 10"><path d="M0 2 H10 V8 H0 Z M0.8 2.6 L5 5.6 L9.2 2.6 V3.4 L5 6.4 L0.8 3.4 Z" fill-rule="evenodd"/></svg>info@tallowridgebuilders.com</li>
        <li><svg viewBox="0 0 10 10"><circle cx="5" cy="5" r="4.5"/></svg>www.tallowridgebuilders.com</li>
      </ul>
    </div>
    <span class="card__edge"></span>
  </section>

  <section class="card card--back" aria-label="Card back">
    <div class="brand">
      <span class="brand__mark"></span>
      <span>Tallow Ridge<br>Builders</span>
    </div>
    <span class="card__edge"></span>
  </section>
</body>
</html>
```